Black Matte card with samurai logo which I would like it to be textured and company name on one side and on the other side I would like the company information with the reno (Face logo) Sushi logo. Double Sided card.

majority customers are University students, University sororities and fraternities.

It Company

Reno Sushi
317 W. Harlow Ave
Tucson, AZ 85042
Phone (520)413-6271
Fax (520)357-1846
E-mail: Renosushidesert@mailbox-example.com
FB: Renosushidesert
Twitter: Renosushidesert

• Present Normal

```html
<!DOCTYPE html>
<html lang="en">
<head>
<meta charset="utf-8">
<title>Reno Sushi – Business Card</title>
<link rel="stylesheet" href="https://fonts.googleapis.com/css2?family=Source+Sans+3:wght@400;600&display=swap">
<style>
  :root {
    --backdrop: #e9e6e1;
    --card-white: #ffffff;
    --ink: #1e1c1d;
    --text-grey: #3a3a3a;
    --brand-red: #d9262a;
    --rule-grey: #b9b9b9;
    --back-dark: #1a1a1a;
    --back-mid: #3a3a3a;
  }
  * { margin: 0; padding: 0; box-sizing: border-box; }
  html, body {
    width: 1200px; height: 1007px; overflow: hidden;
    background: var(--backdrop);
    font-family: "Source Sans 3", "Myriad Pro", sans-serif;
  }
  .canvas { position: relative; width: 1200px; height: 1007px; }

  .card {
    position: absolute; width: 791px; height: 452px;
    border-radius: 38px; overflow: hidden;
    box-shadow: 0 2px 8px rgba(0,0,0,.18);
  }
  .card-front { left: 33px; top: 33px; background: var(--card-white); }
  .card-back {
    left: 298px; top: 514px;
    background: radial-gradient(ellipse at 50% 45%, var(--back-mid) 0%, var(--back-dark) 75%);
  }

  .front-wave { position: absolute; inset: 0; }

  .front-brand {
    position: absolute; left: 70px; top: 215px; width: 220px;
    text-align: center; color: var(--brand-red);
    font-size: 46px; font-weight: 400; line-height: 1;
  }

  .contact-rule {
    position: absolute; left: 382px; top: 100px; width: 1px; height: 150px;
    background: var(--rule-grey);
  }
  .contact-list {
    position: absolute; left: 400px; top: 98px; list-style: none;
    color: var(--text-grey); font-size: 20px; line-height: 30.5px;
  }
  .contact-list li { display: flex; align-items: center; gap: 10px; }
  .contact-icon { width: 18px; height: 18px; flex: none; }

  .address {
    position: absolute; right: 48px; top: 340px; text-align: right;
    color: #fff; font-size: 20px; line-height: 28px;
  }

  .back-brand {
    position: absolute; inset: 0; display: flex; align-items: center;
    justify-content: center; gap: 34px;
    color: var(--brand-red); font-size: 82px; font-weight: 400;
  }
  .back-dot { width: 44px; height: 44px; border-radius: 50%; background: var(--brand-red); }
</style>
</head>
<body>
<main class="canvas">

  <section class="card card-front" aria-label="Card front">
    <svg class="front-wave" viewBox="0 0 791 452" aria-hidden="true">
      <path d="M0,294 C40,380 150,420 300,395 C470,365 620,270 735,295 C765,302 785,315 791,330 L791,452 L0,452 Z" fill="var(--ink)"/>
      <path d="M45,395 C160,440 300,435 460,385 C600,340 720,300 791,322 C720,292 600,320 470,370 C310,425 170,435 45,395 Z" fill="var(--card-white)"/>
    </svg>

    <div class="front-brand">reno sushi</div>

    <div class="contact-rule"></div>
    <ul class="contact-list">
      <li>
        <svg class="contact-icon" viewBox="0 0 18 18" aria-hidden="true"><circle cx="9" cy="9" r="8" fill="none" stroke="var(--brand-red)" stroke-width="1.5"/><path d="M6,5 C5,8 8,12 12,13 L13,11 L11,10 L10,11 C8.5,10 7.5,9 7,7.5 L8,6.5 L7,4.5 Z" fill="var(--brand-red)"/></svg>
        (520)413-6271
      </li>
      <li>
        <svg class="contact-icon" viewBox="0 0 18 18" aria-hidden="true"><rect x="5" y="2" width="8" height="14" rx="1.5" fill="var(--brand-red)"/><rect x="6.5" y="4" width="5" height="4" fill="#fff"/></svg>
        (520)357-1846
      </li>
      <li>
        <svg class="contact-icon" viewBox="0 0 18 18" aria-hidden="true"><rect x="2" y="5" width="14" height="10" rx="1" fill="var(--brand-red)"/><path d="M2,5 L9,11 L16,5" fill="none" stroke="#fff" stroke-width="1.3"/></svg>
        Renosushidesert@mailbox-example.com
      </li>
      <li>
        <svg class="contact-icon" viewBox="0 0 18 18" aria-hidden="true"><rect x="1" y="1" width="16" height="16" rx="2" fill="var(--brand-red)"/></svg>
        Renosushidesert
      </li>
      <li>
        <svg class="contact-icon" viewBox="0 0 18 18" aria-hidden="true"><rect x="1" y="1" width="16" height="16" rx="2" fill="var(--brand-red)"/></svg>
        Renosushidesert
      </li>
    </ul>

    <address class="address" style="font-style:normal">
      Reno Sushi 317<br>
      W. Harlow Ave Tucson<br>
      AZ 85042
    </address>
  </section>

  <section class="card card-back" aria-label="Card back">
    <div class="back-brand">
      <span>reno</span>
      <span class="back-dot"></span>
      <span>sushi</span>
    </div>
  </section>

</main>
</body>
</html>
```